Redesign of Form/Document Navigation Page

I need a redesign of our document and navigation bar on the left. We want the same navigation bar layout/setup but want the buttons and typography to be simple and matching all over. The form needs to be aesthetically pleasing and fit within the page.

1st attachment is our Direct Deposit and the second is the form continued.

```html
<!DOCTYPE html>
<html lang="en">
<head>
<meta charset="utf-8">
<title>Direct Deposit – Sign Document</title>
<link href="https://fonts.googleapis.com/css2?family=Montserrat:wght@500;600;700&family=Raleway:wght@400;500;600;700&display=swap" rel="stylesheet">
<style>
  :root{
    --navy:#25215f;
    --navy-active:#2b3d9f;
    --navy-line:#1f1b52;
    --red:#e5181b;
    --gold:#f3c319;
    --ink:#222;
    --label:#3a3a3a;
    --field:#c9c9cf;
    --white:#fff;
  }
  *{box-sizing:border-box;margin:0;padding:0}
  html,body{width:1200px;height:839px;overflow:hidden;background:var(--white)}
  body{position:relative;font-family:"Raleway",sans-serif;color:var(--ink)}

  .sidebar{position:absolute;left:0;top:0;width:266px;height:798px;background:var(--navy)}
  .brand{position:absolute;left:32px;top:22px;display:flex;align-items:center;gap:12px}
  .brand-dot{width:52px;height:52px;border-radius:50%;background:var(--gold)}
  .brand-name{font-family:"Montserrat",sans-serif;font-weight:600;font-size:16px;line-height:18px;color:var(--gold);text-transform:uppercase;white-space:nowrap}
  .nav{position:absolute;top:105px;left:0;width:266px;list-style:none}
  .nav-item{height:43.6px;display:flex;align-items:center;justify-content:space-between;padding:0 22px 0 57px;font-size:13px;color:#e8e8f4;border-bottom:1px solid var(--navy-line);background:var(--navy);white-space:nowrap}
  .nav-item svg{width:24px;height:24px;stroke:#fff;fill:none;stroke-width:1.4}
  .nav-item.back{background:var(--red);color:#fff;font-weight:700;border-bottom:2px solid #b51013}
  .nav-item.active{background:var(--navy-active)}

  .topbar{position:absolute;left:266px;top:0;width:934px;height:39px;background:var(--red);color:#fff;font-family:"Montserrat",sans-serif;font-weight:600;font-size:12px}
  .topbar-link{position:absolute;top:12px;display:flex;align-items:center;gap:9px;white-space:nowrap}
  .topbar svg{width:13px;height:13px;fill:none;stroke:#fff;stroke-width:1.6}

  .main{position:absolute;left:0;top:0;width:1200px;height:839px}
  .abs{position:absolute}
  .notice-title{left:311px;top:58px;font-size:13px;font-family:"Montserrat",sans-serif;font-weight:600;white-space:nowrap}
  .notice-title span{font-family:"Raleway",sans-serif;font-weight:500;font-size:12.5px;color:#333}
  .notice-text{left:311px;top:84px;width:845px;font-size:9.4px;line-height:18px;color:#333}
  .label{font-family:"Montserrat",sans-serif;font-weight:600;font-size:12.5px;color:var(--label);white-space:nowrap}
  .field{border:1px solid var(--field);border-radius:3px;background:#fff}
  .sign-line{left:314px;top:238px;width:219px;border-top:1px solid #444}
  .btn{display:flex;align-items:center;justify-content:center;color:#fff;font-family:"Montserrat",sans-serif;font-weight:500;font-size:14px;white-space:nowrap}
  .btn-accept{left:313px;top:382px;width:153px;height:32px;background:var(--navy)}
  .btn-submit{left:660px;top:666px;width:93px;height:32px;background:var(--red)}
  .payroll{left:415px;top:466px;width:636px;height:261px;border:1px solid #cfcfd4;border-radius:6px}
  .payroll-title{left:415px;top:486px;width:636px;text-align:center;font-family:"Montserrat",sans-serif;font-weight:600;font-size:13.5px;color:#222}

  .footer{position:absolute;left:0;top:798px;width:1200px;height:41px;background:var(--red);color:#fff;font-family:"Montserrat",sans-serif;font-size:11px}
  .social{position:absolute;top:7px;width:32px;height:30px;background:#fff}
  .copyright{position:absolute;right:66px;top:13px;white-space:nowrap}
  .page-code{position:absolute;right:32px;top:13px}
</style>
</head>
<body>
  <aside class="sidebar">
    <div class="brand"><span class="brand-dot"></span><span class="brand-name">Sentinel Watch<br>Services</span></div>
    <ul class="nav">
      <li class="nav-item back">Back to Profile <svg viewBox="0 0 24 24"><path d="M10 6 4 11l6 5M4 11h9c4 0 6 3 6 7" stroke-width="2.2"/></svg></li>
      <li class="nav-item active">Direct Deposit <svg viewBox="0 0 24 24"><rect x="4" y="4" width="16" height="6"/><path d="M7 10v10h10V10M10 13h4M10 16h4"/></svg></li>
      <li class="nav-item">Change W-4 <svg viewBox="0 0 24 24"><circle cx="12" cy="10" r="6"/><path d="M4 21c1-4 4-6 8-6s7 2 8 6"/></svg></li>
      <li class="nav-item">Labour Code <svg viewBox="0 0 24 24"><circle cx="11" cy="8" r="4"/><path d="M4 20c1-4 3-6 7-6M17 15v6M14 18h6"/></svg></li>
      <li class="nav-item">Personal Information <svg viewBox="0 0 24 24"><rect x="2" y="4" width="20" height="16"/><circle cx="9" cy="11" r="2.5"/><path d="M5 17c1-2 2-3 4-3s3 1 4 3M15 10h4M15 13h4"/></svg></li>
      <li class="nav-item">Appraisal and Review <svg viewBox="0 0 24 24"><rect x="4" y="3" width="14" height="18"/><path d="M7 8l1.5 1.5L11 7M7 13l1.5 1.5L11 12M13 8h3M13 13h3M21 8l-6 10"/></svg></li>
      <li class="nav-item">Write Up-Slip <svg viewBox="0 0 24 24"><path d="M3 10h18v10H3zM3 10l9 5 9-5M8 10l4-6 5 6"/></svg></li>
      <li class="nav-item">Employee Performance <svg viewBox="0 0 24 24"><rect x="4" y="3" width="16" height="14"/><path d="M7 13l3-3 3 2 4-5M8 17l-3 5M16 17l3 5M12 17v5"/></svg></li>
    </ul>
  </aside>

  <header class="topbar">
    <div class="topbar-link" style="left:23px"><svg viewBox="0 0 16 16"><path d="M2 8 8 3l6 5M4 7v6h8V7" fill="#fff"/></svg>HOME</div>
    <div class="topbar-link" style="left:106px"><svg viewBox="0 0 16 16"><circle cx="8" cy="8" r="6"/><circle cx="8" cy="8" r="2.5"/></svg>HELP</div>
    <div class="topbar-link" style="right:46px">DANA REYES <svg viewBox="0 0 16 16"><circle cx="8" cy="5" r="3"/><rect x="3" y="8" width="10" height="7" rx="1"/></svg></div>
  </header>

  <main class="main">
    <p class="abs notice-title">IMPORTANT ! <span>Please read and sign before completing and submitting</span></p>
    <p class="abs notice-text">Nam libero tempore, cum soluta nobis est eligendi optio cumque nihil impedit quo minus id quod maxime placeat facere possimus, omnis voluptas assumenda est, omnis dolor repellendus. Temporibus autem quibusdam et aut officiis debitis aut rerum necessitatibus saepe eveniet ut et voluptates repudiandae sint et molestiae non recusandae. Itaque earum rerum hic tenetur a sapiente delectus.</p>

    <p class="abs label" style="left:314px;top:164px">Emaployee Name : -</p>
    <p class="abs label" style="left:314px;top:191px;color:#222">Employee Signature</p>
    <div class="abs sign-line"></div>
    <div class="abs field" style="left:311px;top:261px;width:224px;height:28px"></div>
    <div class="abs field" style="left:311px;top:307px;width:224px;height:58px"></div>
    <p class="abs label" style="left:569px;top:345px">Sign Date</p>
    <div class="abs field" style="left:640px;top:337px;width:83px;height:28px"></div>
    <div class="abs btn btn-accept">Accept Document</div>

    <section class="abs payroll"></section>
    <p class="abs payroll-title">ONLY PAYROLL MANAGER SIGNS BELOW</p>
    <p class="abs label" style="left:501px;top:532px;color:#222">Company Name</p>
    <div class="abs field" style="left:499px;top:557px;width:196px;height:28px"></div>
    <p class="abs label" style="left:500px;top:594px;color:#222">Employee File Number</p>
    <div class="abs field" style="left:498px;top:618px;width:196px;height:29px"></div>
    <p class="abs label" style="left:722px;top:530px;color:#222">Comments</p>
    <div class="abs field" style="left:720px;top:554px;width:249px;height:90px"></div>
    <div class="abs btn btn-submit">Submit</div>
  </main>

  <footer class="footer">
    <span class="social" style="left:15px"></span>
    <span class="social" style="left:49px"></span>
    <span class="social" style="left:84px"></span>
    <span class="copyright">© 2016. www.sentinelwatch.com</span>
    <span class="page-code">M1</span>
  </footer>
</body>
</html>
```